Steadfast Field Crews

We are a underground coal mining labour hire company, needing a website that links into our online payroll (www.wagelinkr.com.au) and also need to have job applications page that is a preform with drop down menu,s with answers or check boxes. We would also need a 3 tier administration access for access to different files.
We are looking for an ongoing relationship with future app integration

Reason: There are a few more designs to come and I'm out at the mine for another week

Industry/Entity Type

Coal Mining

```html
<!DOCTYPE html>
<html lang="en">
<head>
<meta charset="utf-8">
<title>Steadfast Field Crews</title>
<link href="https://fonts.googleapis.com/css2?family=Open+Sans:wght@400;600;700&display=swap" rel="stylesheet">
<style>
:root{
  --orange:#f26b1d;
  --orange-dark:#d95a10;
  --black:#0a0a0a;
  --nav:#000;
  --text:#555;
  --heading:#222;
  --line:#dcdcdc;
  --band:#efefef;
  --white:#fff;
}
*{margin:0;padding:0;box-sizing:border-box}
html,body{width:746px;height:1200px;overflow:hidden;background:var(--white);font-family:"Open Sans",Arial,sans-serif;color:var(--text)}
.page{position:relative;width:746px;height:1200px}
.abs{position:absolute}
.topbar{left:0;top:0;width:746px;height:72px;background:var(--black)}
.brand-mark{left:82px;top:10px;width:48px;height:50px;display:flex;align-items:center;justify-content:center;gap:4px;color:var(--orange);font-size:9px;font-weight:700}
.brand-mark span.dot{width:10px;height:10px;border-radius:50%;background:var(--orange)}
.search{left:419px;top:27px;width:119px;height:19px;border:1px solid #bbb;border-radius:3px;color:#888;font-size:7px;padding:4px 5px}
.search svg{position:absolute;right:5px;top:3px}
.socials-top{left:568px;top:29px;display:flex;gap:4px}
.socials-top i{width:16px;height:16px;border:1.5px solid var(--orange);display:block}
.nav{left:0;top:72px;width:746px;height:42px;background:var(--nav);border-bottom:3px solid var(--orange)}
.nav ul{list-style:none;display:flex;position:absolute;left:81px;top:0;height:42px}
.nav li{color:var(--white);font-size:8.5px;font-weight:600;display:flex;align-items:center;padding:0 14px;border-right:1px solid #1d1d1d;height:42px}
.nav li.active{color:var(--orange);background:#111}
.hero-photo{left:81px;top:129px;width:393px;height:288px;background:linear-gradient(135deg,#3a3a3a,#1c1a18 55%,#4a3a2c)}
.hero-panel{left:474px;top:129px;width:190px;height:288px;background:var(--orange);color:var(--white);padding:24px 15px 0}
.hero-panel:before{content:"";position:absolute;left:-11px;top:137px;border:11px solid transparent;border-left:0;border-right-color:var(--orange)}
.hero-panel h2{font-size:11.5px;font-weight:600;text-align:center;padding-bottom:9px;border-bottom:1px solid rgba(255,255,255,.4)}
.hero-panel p{font-size:6.8px;line-height:14.5px;margin-top:14px}
.hero-panel .btn{display:block;width:86px;height:20px;margin:26px auto 0;background:#f4f4f4;border-radius:3px;color:#222;font-size:9px;font-weight:600;text-align:center;line-height:20px}
.hero-arrows{position:absolute;left:74px;top:249px;display:flex;gap:6px}
.welcome{left:81px;top:432px;width:583px;text-align:center}
.welcome h1{color:var(--orange);font-size:13px;font-weight:600}
.welcome p{font-size:6.6px;line-height:15px;margin-top:6px;color:#555}
.rule{left:81px;width:583px;height:1px;background:var(--line)}
.col-title{font-size:11px;color:var(--heading)}
.news{left:81px;top:530px;width:147px}
.news h3{padding-bottom:6px;border-bottom:1px solid var(--line);width:138px}
.news-item{margin-top:12px;padding-bottom:10px;border-bottom:1px dotted #bbb;width:147px}
.news-item .thumb{float:left;width:70px;height:38px;background:linear-gradient(135deg,#6b5a4a,#2b2724);margin-right:5px}
.news-item .head{color:var(--orange);font-size:6.8px;line-height:13px;height:42px}
.news-item p{clear:both;font-size:6.8px;line-height:14.5px;margin-top:2px}
.news-item b{font-size:6.8px;color:#222;font-weight:600}
.ug{left:249px;top:532px;width:197px}
.ug .img{margin-top:14px;width:197px;height:102px;background:linear-gradient(135deg,#2a2420,#8a3d16 50%,#1e1a17)}
.ug p{font-size:6.8px;line-height:14.5px;margin-top:9px;text-align:justify}
.eng{left:472px;top:532px;width:192px}
.eng .img{margin-top:14px;width:192px;height:102px;background:linear-gradient(135deg,#2a2a2a,#1a1816 60%,#7a3a18)}
.eng ul{list-style:none;margin-top:6px}
.eng li{font-size:6.8px;height:20.4px;line-height:20px;border-bottom:1px solid #ccc;padding-left:6px;position:relative}
.eng li:before{content:"";position:absolute;left:0;top:8px;border:2px solid transparent;border-left:3px solid var(--orange)}
.btn-o{height:18px;background:var(--orange);color:var(--white);font-size:7px;border-radius:2px;display:flex;align-items:center;gap:6px;padding:0 8px;top:821px}
.btn-o:after{content:"";border:3px solid transparent;border-left:4px solid var(--white);border-right:0}
.services-title{left:81px;top:873px}
.svc-img{left:81px;top:898px;width:163px;height:124px;background:linear-gradient(180deg,#5a2a10,#d46420 60%,#7a3a14)}
.svc-text{left:261px;top:898px;width:403px;font-family:Arial,sans-serif;font-size:7.5px;line-height:15px;color:#777;white-space:nowrap;overflow:hidden}
.svc-list{top:951px;list-style:none;font-size:7px;color:#555}
.svc-list li{height:19.2px;padding-left:10px;position:relative}
.svc-list li:before{content:"";position:absolute;left:0;top:3px;border:3px solid transparent;border-left:5px solid var(--orange)}
.band{left:0;top:1065px;width:746px;height:48px;background:var(--band)}
.follow{left:81px;top:1083px;font-family:Arial,sans-serif;font-size:9.5px;color:#333}
.follow-icons{left:137px;top:1081px;display:flex;gap:6px}
.follow-icons i{width:16px;height:16px;border-radius:50%;display:block;border:2px solid #fff;box-shadow:0 0 0 1px #ccc}
.newsletter{left:349px;top:1083px;font-family:Arial,sans-serif;font-size:9.5px;color:#333}
.email{left:400px;top:1078px;width:205px;height:21px;background:#fff;border:1px solid #ddd;font-size:7.5px;color:#444;padding:5px 8px;font-family:Arial,sans-serif}
.submit{left:612px;top:1078px;width:52px;height:21px;background:var(--orange);color:#fff;font-size:8px;font-weight:700;text-align:center;line-height:21px}
.footer{left:0;top:1113px;width:746px;height:87px;background:var(--orange)}
.foot-brand{left:84px;top:1140px;display:flex;align-items:center;gap:6px;color:#243a8c;font-size:22px;font-weight:600}
.foot-brand i{width:22px;height:22px;background:#243a8c;display:block}
.foot-nav{right:82px;top:1137px;display:flex;gap:9px;font-size:7px;color:#fff}
.copy{right:82px;top:1161px;font-size:6px;color:#fff}
</style>
</head>
<body>
<div class="page">
  <header class="abs topbar"></header>
  <div class="abs brand-mark"><span class="dot"></span>SFC</div>
  <div class="abs search">Search.....
    <svg width="11" height="11" viewBox="0 0 11 11"><circle cx="4.5" cy="4.5" r="3.3" fill="none" stroke="#fff" stroke-width="1.5"/><line x1="7" y1="7" x2="10" y2="10" stroke="#fff" stroke-width="2"/></svg>
  </div>
  <div class="abs socials-top"><i></i><i></i><i></i><i></i><i></i></div>
  <nav class="abs nav"><ul>
    <li class="active">HOME</li><li>APPLY FOR POSITION</li><li style="padding:0 14px 0 18px">PAY PORTAL</li><li style="padding:0 22px 0 14px">DOWNLOAD</li><li style="padding:0 22px">MISSION</li><li style="padding:0 16px 0 18px">ABOUT US</li><li style="padding:0 20px 0 14px">CONTACT US</li>
  </ul></nav>

  <div class="abs hero-photo" role="img" aria-label="Miners in hard hats beside a continuous miner in an underground coal seam"></div>
  <section class="abs hero-panel">
    <h2>IRONVALE MINER COMPANY</h2>
    <p>We are KRVM pty ltd trading as Steadfast Field Crews, we are experienced in ground consolidation in underground coal mines,</p>
    <p>We are KRVM pty ltd trading as Steadfast Field Crews, we are experienced in ground consolidation in underground coal mines,</p>
    <span class="btn">LEARN MORE</span>
    <div class="hero-arrows">
      <svg width="17" height="17" viewBox="0 0 17 17"><circle cx="8.5" cy="8.5" r="7.5" fill="none" stroke="#fff" stroke-width="1.5"/><path d="M10 5 L6 8.5 L10 12Z" fill="#fff"/></svg>
      <svg width="17" height="17" viewBox="0 0 17 17"><circle cx="8.5" cy="8.5" r="7.5" fill="none" stroke="#fff" stroke-width="1.5"/><path d="M7 5 L11 8.5 L7 12Z" fill="#fff"/></svg>
    </div>
  </section>

  <section class="abs welcome">
    <h1>WELCOME TO OUR COMPANY</h1>
    <p>We are KRVM pty ltd trading as Steadfast Field Crews, we are experienced in ground consolidation in underground coal mines, in short when they collapse or<br>cave in we come in with chemical pumps and stabilise the ground or fill cavities which will then allow for the mining process to continue. We also do general mine labor as well.<br>We are a labor hire company for major mining services company, we offer labor solutions in New South Wales and Queensland in the underground coal mines.</p>
  </section>
  <div class="abs rule" style="top:516px"></div>

  <section class="abs news">
    <h3 class="col-title">News &amp; Events</h3>
    <div class="news-item">
      <div class="thumb" role="img" aria-label="Mining equipment close-up"></div>
      <div class="head">Mackay Special Scho<br>nefits from Ridgecore<br>nerosity</div>
      <p>We are a labor hire company for majordf company, we offer labor solutions in gfh and Queensland in the underground coa</p>
      <b>Read More</b>
    </div>
    <div class="news-item">
      <div class="thumb" role="img" aria-label="Hands handling coal samples"></div>
      <div class="head">Mackay Special Scho<br>nefits from Ridgecore<br>nerosity</div>
      <p>We are a labor hire company for majom company, we offer labor solutions in Ne and Queensland in the underground coa and Queensland in the underground coa</p>
      <b>Read More</b>
    </div>
  </section>
  <span class="abs btn-o" style="left:82px">VIEW MORE</span>

  <section class="abs ug">
    <h3 class="col-title">Underground</h3>
    <div class="img" role="img" aria-label="Orange continuous mining machine underground"></div>
    <p>We are a labor hire company for major mining services company, we offer labor solutions in New South Wales and Queensland in the underground coal mines.</p>
    <p style="margin-top:10px">We are a labor hire company for major mining services company, we offer labor solutions in New South Wales and Queensland in the underground coal mines.</p>
    <p style="margin-top:10px">We are a labor hire company for major mining services company, we offer labor solutions.</p>
  </section>
  <span class="abs btn-o" style="left:249px">LEARN MORE</span>

  <section class="abs eng">
    <h3 class="col-title">Engineering</h3>
    <div class="img" role="img" aria-label="Engineers in hard hats inspecting equipment underground"></div>
    <ul>
      <li>JGreat service makes moving things</li><li>Great service makes moving things</li><li>Lock Out Service</li><li>Great service makes moving things</li><li>Recovery &amp; Winch Service</li><li>Great service makes moving things</li><li>Great service makes moving things</li>
    </ul>
  </section>
  <span class="abs btn-o" style="left:472px">LEARN MORE</span>

  <div class="abs rule" style="top:858px"></div>
  <h3 class="abs col-title services-title">Our Services</h3>
  <div class="abs svc-img" role="img" aria-label="Orange-lit longwall conveyor tunnel"></div>
  <p class="abs svc-text">A etiam amet bibendum lorem ipsuxcxm dolor amet craspA etiam amet bibendum lorem ipsuxcxm dolor amet cr<br>A etiam amet bibenzzxdum lorem ipsum dolor amet craspA etiam amet bibendum lorem ipsuxcxm dolor amet c<br>osuere pede placerat, velit neque.........</p>
  <ul class="abs svc-list" style="left:261px">
    <li>Improve talent acquisition</li><li>Reduce time and cost spent interviewing</li><li>Easy to use and completely self-directed</li><li>Customize interview questions</li>
  </ul>
  <ul class="abs svc-list" style="left:453px">
    <li>Improve talent acquisition</li><li>Reduce time and cost spent interviewing</li><li>Easy to use and completely self-directed</li><li>Customize interview questions</li>
  </ul>
  <div class="abs rule" style="top:1042px"></div>

  <div class="abs band"></div>
  <span class="abs follow">Follow us</span>
  <div class="abs follow-icons">
    <i style="background:#c9302c"></i><i style="background:#2a9fd6"></i><i style="background:#d9463b"></i><i style="background:#3b5998"></i><i style="background:#2a7ab8"></i><i style="background:#e8442a"></i>
  </div>
  <span class="abs newsletter">Newsletter</span>
  <div class="abs email">Email</div>
  <div class="abs submit">SUBMIT</div>

  <footer class="abs footer"></footer>
  <div class="abs foot-brand"><i></i>wagelinkr</div>
  <div class="abs foot-nav"><span>Home</span><span>Apply for position</span><span>Pay Portal</span><span>Download</span><span>Mission</span><span>About us</span><span>Contact us</span></div>
  <div class="abs copy">©2014 all copy rights are reserved</div>
</div>
</body>
</html>
```